you will use Ai to Copy the website Brivanta.com to come up with the basic frame work and it will give you the understanding of how I would like Kelbrava.com to be like. Kelbrava.com is a peer to peer rv rental site very similar to both of the other rv rental sites the difference is that are commission based 20% and above per rental and we will be one flat monthly rate and they keep all the earnings. Below is photo that will help you with the color scheme and the look and feel of the design

1 page

```html
<!DOCTYPE html>
<html lang="en">
<head>
<meta charset="utf-8">
<title>Kelbrava.com – Peer to Peer RV Rental</title>
<link href="https://fonts.googleapis.com/css2?family=Playfair+Display:wght@400;500&family=Great+Vibes&family=Inter:wght@400;500;600;700&display=swap" rel="stylesheet">
<style>
:root{
  --navy:#1b2747;
  --navy-deep:#151f3a;
  --green:#5f9e3a;
  --green-light:#7cb342;
  --ink:#222b3a;
  --muted:#555d6b;
  --line:#d9dde3;
  --sand:#f6f2ee;
  --white:#fff;
}
*{box-sizing:border-box;margin:0;padding:0}
html,body{width:1200px;height:4608px;overflow:hidden}
body{position:relative;background:var(--white);font-family:"Inter",sans-serif;color:var(--ink)}
h1,h2,h3,h4{font-weight:400}
.abs{position:absolute}
.photo{position:absolute;overflow:hidden}

/* hero */
.hero{position:absolute;left:0;top:0;width:1200px;height:604px;
  background:linear-gradient(100deg,#152040 0%,#1f2d50 35%,#4a4a55 55%,#b8742e 78%,#f0a23c 92%,#f7c35a 100%)}
.logo{position:absolute;left:89px;top:26px;color:var(--white);font-weight:700;font-size:30px;letter-spacing:-.5px}
.nav a{position:absolute;top:40px;color:var(--white);font-size:13px;text-decoration:none}
.btn-login{position:absolute;left:988px;top:34px;width:84px;height:30px;border-radius:15px;background:var(--green);color:#fff;font-size:12px;display:flex;align-items:center;justify-content:center}
.burger{position:absolute;left:1092px;top:42px}
.hero-h{position:absolute;left:118px;color:#fff;font-family:"Playfair Display",serif;font-weight:400;font-size:50px;line-height:1}
.hero-script{position:absolute;left:106px;top:190px;font-family:"Great Vibes",cursive;color:var(--green-light);font-size:96px;line-height:1}
.hero-p{position:absolute;left:112px;top:340px;width:390px;color:#e6e9ef;font-size:13.5px;line-height:19px}
.search{position:absolute;left:105px;top:474px;width:1000px;height:73px;background:#fff;border-radius:4px}
.field{position:absolute;top:16px}
.field small{display:block;font-size:10.5px;color:var(--muted)}
.field b{display:block;font-size:14px;font-weight:500;margin-top:4px;color:var(--ink)}
.divider{position:absolute;top:0;width:1px;height:73px;background:var(--line)}
.search-go{position:absolute;left:932px;top:7px;width:58px;height:58px;border-radius:50%;background:var(--green);display:flex;align-items:center;justify-content:center}

/* promo */
.promo{top:685px;width:512px;height:359px;border-radius:4px}
.promo-title{position:absolute;left:40px;bottom:22px;color:#fff;font-family:"Playfair Display",serif;font-size:28px}
.pill{position:absolute;background:#fff;color:var(--ink);border-radius:16px;font-size:11px;display:flex;align-items:center;justify-content:center}
.h2{position:absolute;font-family:"Playfair Display",serif;font-size:42px;color:var(--ink);font-weight:400}

/* categories */
.cat{top:1216px;width:318px;height:239px;border-radius:4px}
.cat-title{position:absolute;left:24px;bottom:22px;color:#fff;font-family:"Playfair Display",serif;font-size:24px}
.cat .pill{right:16px;bottom:20px;width:86px;height:28px;font-size:10px}
.track{position:absolute;left:113px;top:1517px;width:978px;height:3px;background:var(--line)}
.track span{display:block;width:271px;height:3px;background:var(--green-light)}

/* featured */
.lead{position:absolute;left:610px;top:1592px;width:500px;font-size:15px;line-height:20px;color:var(--muted)}
.tab{position:absolute;top:1686px;height:47px;border-radius:24px;background:#f1f2f4;color:var(--ink);font-size:15px;display:flex;align-items:center;justify-content:center;gap:8px}
.tab.active{background:var(--navy);color:#fff}
.card{position:absolute;width:240px;height:299px;border:1px solid var(--line);border-radius:3px;background:#fff;box-shadow:0 1px 3px rgba(0,0,0,.08)}
.card .photo{left:0;top:0;width:238px;height:170px}
.fav{position:absolute;right:8px;top:10px;background:#fff;border-radius:10px;font-size:11px;padding:3px 8px}
.card h3{position:absolute;left:26px;top:190px;font-size:12.5px;font-weight:500}
.card p{position:absolute;left:26px;font-size:11.5px;color:var(--muted)}
.card .price{position:absolute;left:26px;top:256px;font-size:14px;font-weight:700}
.btn-more{position:absolute;left:526px;top:2446px;width:171px;height:45px;border-radius:23px;background:var(--green);color:#fff;font-size:15px;display:flex;align-items:center;justify-content:center}

/* destinations */
.band{position:absolute;left:0;top:2566px;width:1200px;height:518px;background:var(--sand)}
.dest{top:2714px;width:310px;height:261px;border-radius:4px}
.dest span{position:absolute;left:26px;bottom:26px;color:#fff;font-family:"Playfair Display",serif;font-size:21px}

/* earnings */
.ring{position:absolute;left:72px;top:3138px;width:536px;height:536px;border-radius:50%;background:#e4e6ea;padding:16px}
.ring .photo{position:static;width:504px;height:504px;border-radius:50%;background:linear-gradient(180deg,#3f6f8c 0%,#5b8a5a 35%,#2f4f3a 55%,#d9dde0 62%,#e8e9ea 75%,#6b6e70 88%,#8a8c8e 100%)}
.earn-h{position:absolute;left:656px;top:3170px;font-family:"Playfair Display",serif;font-weight:400;font-size:46px;line-height:54px;color:var(--ink)}
.earn-p{position:absolute;left:662px;font-size:16.5px;line-height:24px;color:var(--muted);width:460px}
.feat{position:absolute;left:662px;display:flex;align-items:center;gap:24px;font-size:15px;font-weight:600;letter-spacing:.6px;color:var(--navy)}
.feat-line{position:absolute;left:662px;width:340px;height:1px;background:var(--line)}

/* cities */
.city{position:absolute;display:flex;gap:8px}
.city b{display:block;font-size:14px;font-weight:500;color:var(--ink)}
.city small{display:block;font-size:13.5px;color:var(--muted);margin-top:8px}

/* footer */
.footer{position:absolute;left:0;top:4179px;width:1200px;height:429px;background:var(--navy-deep)}
.social{position:absolute;top:4324px;width:26px;height:26px;border-radius:50%;background:#fff}
.fcol{position:absolute;top:4254px;color:#fff}
.fcol h4{font-size:14px;font-weight:600;margin-bottom:14px}
.fcol a{display:block;color:#c9cfdb;font-size:12px;line-height:25px;text-decoration:none}
.frule{position:absolute;left:0;top:4515px;width:1200px;height:2px;background:var(--green)}
.fbottom{position:absolute;top:4537px;color:#c9cfdb;font-size:12px}
</style>
</head>
<body>

<!-- HERO -->
<section class="hero" role="img" aria-label="Motorhome driving a mountain road at sunset"></section>
<div class="logo">Kelbrava.com</div>
<nav class="nav">
  <a style="left:407px">Find an RV</a>
  <a style="left:523px">List Your RV</a>
  <a style="left:647px">How it Works</a>
  <a style="left:780px">Resources</a>
  <a style="left:900px">
    <svg width="12" height="12" viewBox="0 0 12 12" style="vertical-align:-1px"><circle cx="6" cy="3.5" r="2.6" fill="#fff"/><path d="M1 12c0-3 2.2-4.8 5-4.8s5 1.8 5 4.8z" fill="#fff"/></svg>
    Sign Up</a>
</nav>
<div class="btn-login">Log In</div>
<svg class="burger" width="20" height="14" viewBox="0 0 20 14"><path d="M0 1h20M0 7h20M0 13h20" stroke="#fff" stroke-width="2"/></svg>

<h1 class="hero-h" style="top:146px">Your Next</h1>
<div class="hero-script">Adventure</div>
<div class="hero-h" style="top:264px">Starts Here</div>
<p class="hero-p">Find the perfect RV for your next road trip, weekend get-away, or cross-country adventure. Rent directly from RV owners and discover a better way to explore.</p>

<div class="search">
  <div class="field" style="left:33px"><small>Location</small><b>Amsterdam, NH</b></div>
  <svg class="abs" style="left:298px;top:32px" width="10" height="10" viewBox="0 0 10 10"><path d="M1 1l8 8M9 1l-8 8" stroke="#aaa" stroke-width="1.3"/></svg>
  <div class="divider" style="left:326px"></div>
  <div class="field" style="left:350px"><small>Dates</small><b>Any Dates</b></div>
  <div class="divider" style="left:512px"></div>
  <div class="field" style="left:532px"><small>Guests</small><b>2 guests</b></div>
  <div class="divider" style="left:655px"></div>
  <div class="field" style="left:671px"><small>Driver's age</small><b>25+</b></div>
  <div class="divider" style="left:778px"></div>
  <div class="field" style="left:801px"><small>Rental Type</small><b>All Type</b></div>
  <div class="search-go"><svg width="22" height="22" viewBox="0 0 22 22"><circle cx="9.5" cy="9.5" r="6.5" fill="none" stroke="#fff" stroke-width="2"/><path d="M14.5 14.5l5 5" stroke="#fff" stroke-width="2.2" stroke-linecap="round"/></svg></div>
</div>

<!-- PROMO CARDS -->
<div class="photo promo" style="left:91px;background:linear-gradient(180deg,#8a7f74 0%,#b5aa9a 35%,#dfe1e3 55%,#6f7b5e 85%,#555d48 100%)" role="img" aria-label="Pickup truck towing a travel trailer on a hillside">
  <span class="promo-title">Drive it or Tow it</span>
  <span class="pill" style="right:44px;bottom:24px;width:104px;height:30px">Book Now</span>
</div>
<div class="photo promo" style="left:620px;background:linear-gradient(180deg,#2f4a2a 0%,#4c6a3a 40%,#7b7d72 60%,#3e4a36 100%)" role="img" aria-label="Trailer set up at a forest campsite with awning and chairs">
  <span class="promo-title" style="left:26px;bottom:30px">Delivery &amp; On-Site Stays</span>
  <span class="pill" style="right:22px;bottom:28px;width:98px;height:30px">Pick it up</span>
</div>

<!-- FIND YOUR PERFECT RV -->
<h2 class="h2" style="left:97px;top:1115px">Find Your Perfect RV</h2>
<div class="photo cat" style="left:100px;background:linear-gradient(180deg,#6f8f5a 0%,#e9ebec 40%,#c8cbcd 65%,#7a8f4a 100%)" role="img" aria-label="Class C motorhome parked in a meadow">
  <span class="cat-title">Travel Trailers</span><span class="pill">Book now</span>
</div>
<div class="photo cat" style="left:434px;background:linear-gradient(180deg,#4f7a3a 0%,#dfe3e6 45%,#a7b0b5 65%,#4d7a2f 100%)" role="img" aria-label="Camper trailer parked on grass under trees">
  <span class="cat-title">Camper Trailers</span><span class="pill" style="background:var(--green);color:#fff">Book now</span>
</div>
<div class="photo cat" style="left:767px;background:linear-gradient(180deg,#5c7a48 0%,#e2e4e6 45%,#b0b5b8 65%,#6d7660 100%)" role="img" aria-label="Fifth wheel trailer hitched to a pickup">
  <span class="cat-title">Fifth Wheels</span><span class="pill">Book now</span>
</div>
<div class="photo cat" style="left:1101px;background:linear-gradient(180deg,#4a6f9a 0%,#dfe2e5 50%,#5a7a48 100%)" role="img" aria-label="Fifth wheel trailer by mountains">
  <span class="cat-title">Fifth Wheels</span>
</div>
<div class="track"><span></span></div>

<!-- FEATURED -->
<h2 class="h2" style="left:111px;top:1584px">Featured RV Rental</h2>
<p class="lead">From compact campervans to spacious motorhomes, discover RVs that fit your trip, your crew, and your travel style.</p>

<div class="tab active" style="left:123px;width:177px">
  <svg width="14" height="13" viewBox="0 0 14 13"><path d="M7 12S1 8 1 4.2A3 3 0 0 1 7 3a3 3 0 0 1 6 1.2C13 8 7 12 7 12z" fill="none" stroke="#fff" stroke-width="1.3"/></svg>Popular</div>
<div class="tab" style="left:324px;width:176px">
  <svg width="22" height="14" viewBox="0 0 22 14"><rect x="1" y="2" width="18" height="9" rx="2" fill="none" stroke="#333" stroke-width="1.2"/><path d="M4 5h4M10 5h4" stroke="#333" stroke-width="1.2"/><circle cx="6" cy="12" r="1.6" fill="#333"/><circle cx="15" cy="12" r="1.6" fill="#333"/></svg>Camper Van</div>
<div class="tab" style="left:513px;width:175px">
  <svg width="14" height="14" viewBox="0 0 14 14"><path d="M1 7V1h6l6 6-6 6z" fill="none" stroke="#333" stroke-width="1.2"/><circle cx="4" cy="4" r="1" fill="#333"/></svg>Values</div>
<div class="tab" style="left:699px;width:177px">
  <svg width="18" height="13" viewBox="0 0 18 13"><rect x="1" y="1" width="14" height="9" rx="2" fill="none" stroke="#333" stroke-width="1.2"/><path d="M4 4h8" stroke="#333" stroke-width="1.2"/><circle cx="5" cy="11" r="1.5" fill="#333"/></svg>Vintage</div>
<div class="tab" style="left:889px;width:191px">
  <svg width="20" height="13" viewBox="0 0 20 13"><rect x="1" y="1" width="13" height="8" rx="1.5" fill="none" stroke="#333" stroke-width="1.2"/><path d="M14 7h5" stroke="#333" stroke-width="1.2"/><circle cx="6" cy="10.5" r="1.6" fill="#333"/></svg>Small Trailers</div>

<!-- row 1 -->
<article class="card" style="left:114px;top:1788px">
  <div class="photo" style="background:linear-gradient(180deg,#c9773e 0%,#a6552d 40%,#e6e8ea 60%,#8e6a3a 100%)" role="img" aria-label="Class C motorhome in red hills"></div>
  <span class="fav">60 ♡</span>
  <h3>2024 Wind Jamming Talvora</h3><p style="top:208px">Fifth Wheel</p><p style="top:227px">Lynn Haven FL</p><span class="price">$110 / night</span>
</article>
<article class="card" style="left:374px;top:1788px">
  <div class="photo" style="background:linear-gradient(180deg,#5e86b0 0%,#e8eaec 45%,#c9cdd1 70%,#6e7a6a 100%)" role="img" aria-label="White motorhome on a road"></div>
  <span class="fav">60 ♡</span>
  <h3>2024 Wind Jamming Talvora</h3><p style="top:208px">Camper Van</p><p style="top:227px">Lynn Haven FL</p><span class="price">$110 / night</span>
</article>
<article class="card" style="left:633px;top:1788px">
  <div class="photo" style="background:linear-gradient(180deg,#3f5f3a 0%,#e4e6e8 45%,#bfc3c6 70%,#5d7a44 100%)" role="img" aria-label="Travel trailer parked by trees"></div>
  <span class="fav">60 ♡</span>
  <h3>2024 Wind Jamming Talvora</h3><p style="top:208px">Travel Trailer</p><p style="top:227px">Lynn Haven FL</p><span class="price">$110 / night</span>
</article>
<article class="card" style="left:892px;top:1788px">
  <div class="photo" style="background:linear-gradient(180deg,#c98a3a 0%,#6a5a3a 40%,#dfe1e3 60%,#7d8084 100%)" role="img" aria-label="Camper by autumn trees"></div>
  <span class="fav">60 ♡</span>
  <h3>2024 Wind Jamming Talvora</h3><p style="top:208px">Camper Van</p><p style="top:227px">Lynn Haven FL</p><span class="price">$110 / night</span>
</article>
<!-- row 2 -->
<article class="card" style="left:114px;top:2108px">
  <div class="photo" style="background:linear-gradient(180deg,#6a93c4 0%,#eceeef 45%,#c8ccce 70%,#7a9a4a 100%)" role="img" aria-label="Caravan by a mountain lake"></div>
  <span class="fav">60 ♡</span>
  <h3>2024 Wind Jamming Talvora</h3><p style="top:208px">Fifth Wheel</p><p style="top:227px">Lynn Haven FL</p><span class="price">$110 / night</span>
</article>
<article class="card" style="left:374px;top:2108px">
  <div class="photo" style="background:linear-gradient(180deg,#4a7a3a 0%,#e9ebec 45%,#c4c8ca 70%,#6a6e70 100%)" role="img" aria-label="Caravan in a forest clearing"></div>
  <span class="fav">60 ♡</span>
  <h3>2024 Wind Jamming Talvora</h3><p style="top:208px">Fifth Wheel</p><p style="top:227px">Lynn Haven FL</p><span class="price">$110 / night</span>
</article>
<article class="card" style="left:633px;top:2108px">
  <div class="photo" style="background:linear-gradient(180deg,#5a8fc8 0%,#8cb0d8 30%,#e6e8ea 50%,#7aa84a 75%,#5f8f38 100%)" role="img" aria-label="Caravan on a green field"></div>
  <span class="fav">60 ♡</span>
  <h3>2024 Wind Jamming Talvora</h3><p style="top:208px">v</p><p style="top:227px">Lynn Haven FL</p><span class="price">$110 / night</span>
</article>
<article class="card" style="left:892px;top:2108px">
  <div class="photo" style="background:linear-gradient(180deg,#8a9aa8 0%,#e8eaec 45%,#c2c6c9 70%,#8a8e90 100%)" role="img" aria-label="Caravan parked by a house"></div>
  <span class="fav">60 ♡</span>
  <h3>2024 Wind Jamming Talvora</h3><p style="top:208px">Fifth Wheel</p><p style="top:227px">Lynn Haven FL</p><span class="price">$110 / night</span>
</article>
<div class="btn-more">View More</div>

<!-- DESTINATIONS -->
<section class="band"></section>
<h2 class="h2" style="left:0;width:1200px;text-align:center;top:2618px;font-size:46px">Popular Desitnations</h2>
<svg class="abs" style="left:54px;top:2818px" width="24" height="44" viewBox="0 0 24 44"><path d="M20 2L4 22l16 20" fill="none" stroke="var(--green)" stroke-width="2.5"/></svg>
<svg class="abs" style="left:1111px;top:2818px" width="24" height="44" viewBox="0 0 24 44"><path d="M4 2l16 20L4 42" fill="none" stroke="var(--green)" stroke-width="2.5"/></svg>
<div class="photo dest" style="left:113px;background:linear-gradient(180deg,#5a8ac0 0%,#9a9f9a 35%,#3f5a3a 65%,#2f3a2a 100%)" role="img" aria-label="Yosemite valley with granite cliffs and a river"><span>Yosemite, CA</span></div>
<div class="photo dest" style="left:445px;background:linear-gradient(180deg,#3f7fd0 0%,#c9d8e8 30%,#4a6f7a 55%,#6f9a3a 80%,#5a8a2f 100%)" role="img" aria-label="Green hills below mountains"><span>Hill Country, TX</span></div>
<div class="photo dest" style="left:778px;background:linear-gradient(180deg,#8aa8c8 0%,#d8662a 35%,#c9a070 60%,#5a6a7a 100%)" role="img" aria-label="Lakeside houses with autumn trees"><span>Bayfield, CO</span></div>

<!-- EARNINGS -->
<div class="ring"><div class="photo" role="img" aria-label="Motorhome driving along a lakeside road with forested hills"></div></div>
<h2 class="earn-h">Your RV.<br>Your Earnings.</h2>
<p class="earn-p" style="top:3300px">Why give away a large percentage of every rental?</p>
<p class="earn-p" style="top:3333px">Kelbrava offers RV owners a simpler alternative to commission-based rental marketplaces. Instead of losing 20% or more from each rental, you pay one flat monthly rate and keep your rental earnings.</p>

<div class="feat" style="top:3468px">
  <svg width="30" height="32" viewBox="0 0 30 32"><rect x="2" y="5" width="26" height="25" rx="3" fill="var(--green)"/><rect x="2" y="5" width="26" height="6" fill="#4a8a2a"/><path d="M8 2v6M22 2v6" stroke="var(--green)" stroke-width="3" stroke-linecap="round"/><text x="15" y="26" text-anchor="middle" font-family="Inter,sans-serif" font-size="13" font-weight="700" fill="#fff">$</text></svg>
  ONE FLAT MONTHLY RATE</div>
<div class="feat-line" style="top:3515px"></div>
<div class="feat" style="top:3528px">
  <svg width="30" height="32" viewBox="0 0 30 32"><circle cx="17" cy="10" r="8" fill="var(--green)"/><text x="17" y="14.5" text-anchor="middle" font-family="Inter,sans-serif" font-size="11" font-weight="700" fill="#fff">$</text><path d="M2 24h8l5 2h8c2 0 2 3 0 3H12" fill="none" stroke="var(--green)" stroke-width="2.4" stroke-linecap="round"/></svg>
  KEEP YOUR RENTAL EARNINGS</div>
<div class="feat-line" style="top:3575px"></div>
<div class="feat" style="top:3588px">
  <svg width="30" height="32" viewBox="0 0 30 32"><circle cx="15" cy="16" r="10" fill="none" stroke="var(--green)" stroke-width="5" stroke-dasharray="4 3"/><circle cx="15" cy="16" r="8" fill="var(--green)"/><circle cx="15" cy="16" r="3.5" fill="#fff"/></svg>
  YOU STAY IN CONTROL</div>

<!-- CITIES -->
<h2 class="h2" style="left:105px;top:3766px;font-size:38px">Popular RV Rental Desitnation</h2>
<svg width="0" height="0" style="position:absolute"><defs><symbol id="pin" viewBox="0 0 16 20"><path d="M8 19s6-6.5 6-11A6 6 0 0 0 2 8c0 4.5 6 11 6 11z" fill="none" stroke="#6b7280" stroke-width="1.4"/><circle cx="8" cy="8" r="2.2" fill="none" stroke="#6b7280" stroke-width="1.4"/></symbol></defs></svg>

<div class="city" style="left:107px;top:3865px"><svg width="16" height="20"><use href="#pin"/></svg><div><b>Atlanta, GA</b><small>751 RV rentals</small></div></div>
<div class="city" style="left:311px;top:3865px"><svg width="16" height="20"><use href="#pin"/></svg><div><b>Chicago, IL</b><small>455 RV rentals</small></div></div>
<div class="city" style="left:524px;top:3865px"><svg width="16" height="20"><use href="#pin"/></svg><div><b>Houston, TX</b><small>567 RV rentals</small></div></div>
<div class="city" style="left:737px;top:3865px"><svg width="16" height="20"><use href="#pin"/></svg><div><b>Las Vegas, NV</b><small>436 RV rentals</small></div></div>
<div class="city" style="left:942px;top:3865px"><svg width="16" height="20"><use href="#pin"/></svg><div><b>New York, NY</b><small>436 RV rentals</small></div></div>

<div class="city" style="left:107px;top:3944px"><svg width="16" height="20"><use href="#pin"/></svg><div><b>Austin, TX</b><small>783 RV rentals</small></div></div>
<div class="city" style="left:311px;top:3944px"><svg width="16" height="20"><use href="#pin"/></svg><div><b>Columbus, OH</b><small>410 RV rentals</small></div></div>
<div class="city" style="left:524px;top:3944px"><svg width="16" height="20"><use href="#pin"/></svg><div><b>Kailua-Kona, HI</b><small>148 RV rentals</small></div></div>
<div class="city" style="left:737px;top:3944px"><svg width="16" height="20"><use href="#pin"/></svg><div><b>Maui, HI</b><small>149 RV rentals</small></div></div>
<div class="city" style="left:942px;top:3944px"><svg width="16" height="20"><use href="#pin"/></svg><div><b>Oklahoma City, OK</b><small>149 RV rentals</small></div></div>

<div class="city" style="left:107px;top:4022px"><svg width="16" height="20"><use href="#pin"/></svg><div><b>Boston, MA</b><small>351 RV rentals</small></div></div>
<div class="city" style="left:311px;top:4022px"><svg width="16" height="20"><use href="#pin"/></svg><div><b>Dallas, TX</b><small>715 RV rentals</small></div></div>
<div class="city" style="left:524px;top:4022px"><svg width="16" height="20"><use href="#pin"/></svg><div><b>Kauai, HI</b><small>82 RV rentals</small></div></div>
<div class="city" style="left:737px;top:4022px"><svg width="16" height="20"><use href="#pin"/></svg><div><b>Nashville, TN</b><small>311 RV rentals</small></div></div>
<div class="city" style="left:942px;top:4022px"><svg width="16" height="20"><use href="#pin"/></svg><div><b>Orlando, FL</b><small>311 RV rentals</small></div></div>

<!-- FOOTER -->
<footer class="footer"></footer>
<div class="logo" style="top:4256px;left:93px;font-size:28px">Kelbrava.com</div>
<span class="social" style="left:107px"></span>
<span class="social" style="left:143px"></span>
<span class="social" style="left:179px"></span>
<span class="social" style="left:215px"></span>
<span class="social" style="left:251px"></span>

<div class="fcol" style="left:388px"><h4>Navigation</h4><a>Where it all began</a><a>Careers</a><a>Stories and news</a><a>Travel journal</a><a>About</a></div>
<div class="fcol" style="left:583px"><h4>Guest travel</h4><a>Group bookings</a><a>National park guides</a><a>One-way rentals</a><a>Road trip guides</a><a>RV parks &amp; campgrounds</a><a>Guide to all RV types</a></div>
<div class="fcol" style="left:799px"><h4>Hosting</h4><a>Become an RV host</a><a>Fleetline demo</a><a>Affiliate program</a><a>RV insurance</a><a>Host mobile app</a><a>Host tablet app</a></div>
<div class="fcol" style="left:994px"><h4>Support</h4><a>How it works</a><a>Help center</a><a>LLM info</a><a>Contact</a></div>

<div class="frule"></div>
<div class="fbottom" style="left:102px">© 2026 Kelbrava. All rights reserved.</div>
<div class="fbottom" style="left:910px">Terms &nbsp;|&nbsp; Privacy &nbsp;|&nbsp; Sitemap</div>

</body>
</html>
```